QP Fiduciary Website Redesign Contest

We want to refresh our website to be more insitutional, professional for an international audience. We have designed a new logo for this purpose and that has been attached. A full brand brief and positioning statement has also been attached. Please read through all the documents carefully before designing. The old website is found here: https://qp-fiduciary.example/

Target Market(s)

Actuaries and associated businesses internationally

Industry/Entity Type

professional services - actuaries

Number of Pages Required

3 page

Font styles to use
Sans Serif

Colors
0054AA
0677BA
7BADD7
CADEEF
E8F1F8
0094D4
00A9DD
6FCCEA
C7EBF8
E9F6FB
F0912C
F2A743
F7CA91
FBE8D2
FDF5EE
EE7325
F08F49
F5BC92
FAE3D3
FDF4ED
EB3D1F
EC4F4E
F09395
F8D3D4
FCEDEE

Requirements
Must have
• blues and greens to match the logo color, complimentary colors, navigation
Nice to have
• old site: https://qp-fiduciary.example/

```html
<!DOCTYPE html>
<html lang="en">
<head>
<meta charset="utf-8">
<title>QP Fiduciary — Actuarial Software</title>
<link href="https://fonts.googleapis.com/css2?family=Michroma&family=Inter:wght@400;500;600;700&display=swap" rel="stylesheet">
<style>
:root{
  --blue-deep:#0a2f86;
  --blue:#0054aa;
  --blue-ink:#0b4aa8;
  --blue-pale:#e4edf7;
  --orange:#ee7325;
  --ink:#1f2733;
  --white:#ffffff;
  --grey-text:#3a3f48;
}
*{box-sizing:border-box;margin:0;padding:0}
html,body{width:1200px;height:3415px;overflow:hidden}
body{position:relative;font-family:"Inter",Arial,sans-serif;color:var(--ink);background:var(--white)}
.abs{position:absolute}
.display{font-family:"Michroma","Inter",sans-serif;font-weight:400;letter-spacing:1px;text-transform:uppercase}
.btn{position:absolute;background:var(--orange);color:var(--white);border-radius:16px;font-weight:600;font-size:13px;display:flex;align-items:center;justify-content:center;white-space:nowrap}
.wordmark{font-family:"Inter",Arial,sans-serif;font-weight:700;color:var(--blue);display:flex;align-items:center;gap:10px;font-size:26px}
.wordmark .dot{width:18px;height:18px;border-radius:50%;background:var(--orange)}

/* header */
.site-header{position:absolute;left:0;top:0;width:1200px;height:91px;background:var(--white)}
.site-header .wordmark{position:absolute;left:103px;top:27px}
.nav-active{position:absolute;left:379px;top:0;width:73px;height:3px;background:var(--orange)}
.main-nav a{position:absolute;top:38px;font-size:13px;color:var(--ink);text-decoration:none}

/* hero */
.hero{position:absolute;left:0;top:91px;width:1200px;height:533px;
  background:radial-gradient(ellipse at 55% 20%,#1f5fd0 0%,#0d3f9e 45%,#082a78 100%)}
.hero-title{position:absolute;left:0;width:1200px;top:170px;text-align:center;color:var(--white);font-size:24px;line-height:34px}
.hero-sub{position:absolute;left:180px;width:840px;top:250px;text-align:center;color:var(--white);font-size:20px;line-height:29px}
.hero-arrow{position:absolute;top:222px}

/* overview */
.overview-text{position:absolute;left:0;top:624px;width:600px;height:373px;background:var(--white)}
.overview-diagram{position:absolute;left:600px;top:624px;width:600px;height:373px;
  background:radial-gradient(ellipse at 55% 50%,#f2f6fb 0%,#e4edf7 60%,#dbe7f4 100%)}
.section-title{color:var(--blue);font-size:24px}
.overview-text .section-title{position:absolute;left:102px;top:120px}
.overview-text p{position:absolute;left:102px;top:164px;width:480px;font-size:13px;line-height:21px;color:var(--grey-text)}

/* core solutions */
.solutions{position:absolute;left:0;top:997px;width:1200px;height:671px;
  background:radial-gradient(ellipse at 70% 60%,#1a6ee6 0%,#0a55c8 40%,#0842a8 100%)}
.solutions .section-title{position:absolute;left:0;width:1200px;top:93px;text-align:center;color:var(--white)}
.solution{position:absolute;top:236px;width:300px;text-align:center;color:var(--white)}
.solution h3{font-size:22px;font-weight:700;line-height:34px;height:68px;display:flex;align-items:center;justify-content:center}
.solution .icon{margin:12px auto 0;display:block}
.solution p{font-size:15px;line-height:25px;margin-top:14px}
.divider{position:absolute;top:223px;width:1px;height:318px;background:rgba(255,255,255,.35)}

/* characteristics */
.characteristics{position:absolute;left:0;top:1668px;width:1200px;height:501px;
  background:linear-gradient(180deg,#f4f6fa 0%,#ffffff 100%)}
.characteristics .section-title{position:absolute;left:0;width:1200px;top:105px;text-align:center}
.trait-num{position:absolute;width:76px;height:76px;border-radius:50%;background:var(--blue-ink);color:var(--white);
  font-family:"Michroma",sans-serif;font-size:22px;display:flex;align-items:center;justify-content:center}
.trait-num.accent{background:var(--orange)}
.trait-text{position:absolute;font-size:14px;font-weight:700;line-height:21px;color:var(--blue-ink)}

/* insights */
.insights{position:absolute;left:0;top:2169px;width:1200px;height:544px;background:var(--white)}
.insights .section-title{position:absolute;left:0;width:1200px;top:62px;text-align:center}
.insight-card{position:absolute;top:138px;width:318px;height:334px;overflow:hidden}
.insight-card h4{position:absolute;left:32px;bottom:28px;right:28px;color:var(--white);font-size:20px;font-weight:700;line-height:25px}
.card-a{left:102px;background:linear-gradient(150deg,#2a0f3a 0%,#4a2a8a 45%,#0c2f7a 100%)}
.card-b{left:441px;background:linear-gradient(160deg,#7c8d92 0%,#2f4a52 40%,#0a0d10 100%)}
.card-c{left:780px;background:linear-gradient(150deg,#b9d4f0 0%,#d9231e 35%,#8a0d0a 100%)}

/* cta */
.cta{position:absolute;left:0;top:2713px;width:1200px;height:444px;
  background:radial-gradient(ellipse at 50% 30%,#1c5bd0 0%,#0b3a9e 55%,#082a78 100%)}
.cta .display{position:absolute;left:0;width:1200px;top:136px;text-align:center;color:var(--white);font-size:24px}

/* footer */
.site-footer{position:absolute;left:0;top:3157px;width:1200px;height:258px;background:#eef3f9}
.site-footer .wordmark{position:absolute;left:0;width:1200px;justify-content:center;top:68px}
.footer-nav a{position:absolute;top:139px;font-size:17px;color:var(--ink);text-decoration:none}
.social{position:absolute;left:830px;top:141px;width:16px;height:16px;background:var(--ink);border-radius:2px}
.copyright{position:absolute;left:0;width:1200px;top:184px;text-align:center;font-size:17px;color:var(--ink)}
</style>
</head>
<body>

<header class="site-header">
  <div class="nav-active"></div>
  <div class="wordmark"><span>QP Fiduciary</span><span class="dot"></span></div>
  <nav class="main-nav">
    <a style="left:397px">Home</a>
    <a style="left:463px">Platform</a>
    <a style="left:545px">Solutions</a>
    <a style="left:631px">Insights</a>
    <a style="left:710px">Company</a>
    <a style="left:797px">Contact</a>
  </nav>
  <div class="btn" style="left:871px;top:30px;width:226px;height:32px">Request Technical Walkthrough</div>
</header>

<section class="hero" role="img" aria-label="Abstract deep blue architectural lines background">
  <svg class="hero-arrow" style="left:104px" width="20" height="34" viewBox="0 0 20 34"><path d="M16 3 L4 17 L16 31" stroke="#fff" stroke-width="4" fill="none" stroke-linecap="round"/></svg>
  <svg class="hero-arrow" style="left:1071px" width="20" height="34" viewBox="0 0 20 34"><path d="M4 3 L16 17 L4 31" stroke="#fff" stroke-width="4" fill="none" stroke-linecap="round"/></svg>
  <h1 class="hero-title display">Actuarial software for structured,<br>auditable financial analysis</h1>
  <p class="hero-sub">Software that translates actuarial methodologies into disciplined decision-ready analytical tools across diverse regulatory environments</p>
  <div class="btn" style="left:488px;top:331px;width:225px;height:31px">Request Technical Walkthrough</div>
</section>

<section class="overview-text">
  <h2 class="section-title display">Platform Overview</h2>
  <p>QP Fiduciary develops modular actuarial software designed to support reserving, valuation, pricing, and risk analysis workflows across diverse regulatory environments.</p>
  <div class="btn" style="left:102px;top:242px;width:149px;height:31px">Explore Platform</div>
</section>

<section class="overview-diagram" role="img" aria-label="Illustration of the platform linking reserving, valuation, pricing and risk analysis"></section>

<section class="solutions">
  <h2 class="section-title display">Core Solutions</h2>
  <div class="divider" style="left:430px"></div>
  <div class="divider" style="left:770px"></div>

  <div class="solution" style="left:111px">
    <h3>Reserving &amp;<br>Valuation</h3>
    <svg class="icon" width="82" height="82" viewBox="0 0 82 82"><circle cx="41" cy="41" r="39" fill="none" stroke="#fff" stroke-width="2"/><rect x="30" y="22" width="24" height="32" rx="2" fill="none" stroke="#fff" stroke-width="2"/><path d="M35 46v-6M40 46v-10M45 46v-8" stroke="#fff" stroke-width="2"/><circle cx="30" cy="52" r="6" fill="none" stroke="#fff" stroke-width="2"/><path d="M26 56 20 62" stroke="#fff" stroke-width="2"/></svg>
    <p>Software supporting structured<br>reserving workflows<br>and financial reporting across<br>jurisdictions</p>
  </div>

  <div class="solution" style="left:449px">
    <h3>Pricing</h3>
    <svg class="icon" width="96" height="96" viewBox="0 0 96 96"><circle cx="48" cy="48" r="47" fill="#ee7325" stroke="#fff" stroke-width="2"/><rect x="24" y="34" width="48" height="28" rx="3" fill="none" stroke="#fff" stroke-width="2.5"/><circle cx="48" cy="48" r="9" fill="none" stroke="#fff" stroke-width="2.5"/><path d="M28 30h44" stroke="#fff" stroke-width="2.5"/></svg>
    <p>Software supporting structured<br>reserving workflows<br>and financial reporting across<br>jurisdictions</p>
  </div>

  <div class="solution" style="left:791px">
    <h3>Enterprise Risk<br>Management</h3>
    <svg class="icon" width="82" height="82" viewBox="0 0 82 82"><circle cx="41" cy="41" r="39" fill="none" stroke="#fff" stroke-width="2"/><path d="M34 16 22 38h24z" fill="none" stroke="#fff" stroke-width="2"/><path d="M34 24v7M34 34v1" stroke="#fff" stroke-width="2"/><circle cx="50" cy="36" r="9" fill="none" stroke="#fff" stroke-width="2"/><path d="M18 50c8 0 12 6 20 6h14l10-8" fill="none" stroke="#fff" stroke-width="2"/></svg>
    <p>Software supporting reinsurance<br>optimization and capital modeling.</p>
  </div>
</section>

<section class="characteristics">
  <h2 class="section-title display">Platform Characteristics</h2>
  <div class="trait-num" style="left:104px;top:226px">01</div>
  <div class="trait-text" style="left:191px;top:228px">Structured workflows<br>suitable for<br>multi-jurisdictional<br>review</div>
  <div class="trait-num accent" style="left:356px;top:291px">02</div>
  <div class="trait-text" style="left:441px;top:289px">Transparent<br>assumptions and<br>methodological clarity</div>
  <div class="trait-num" style="left:610px;top:241px">03</div>
  <div class="trait-text" style="left:696px;top:258px">Comparative scenario<br>analysis</div>
  <div class="trait-num" style="left:866px;top:295px">04</div>
  <div class="trait-text" style="left:951px;top:305px">Supports professional<br>judgment rather than<br>replacing it</div>
</section>

<section class="insights">
  <h2 class="section-title display">Insights</h2>
  <article class="insight-card card-a" role="img" aria-label="Abstract glowing data wave photograph">
    <svg class="abs" style="right:32px;top:30px" width="28" height="28" viewBox="0 0 28 28"><path d="M3 25 25 3M10 3h15v15" stroke="#fff" stroke-width="2" fill="none"/></svg>
    <h4 style="bottom:52px">Methodological<br>perspectives in actuarial<br>reserving</h4>
  </article>
  <article class="insight-card card-b" role="img" aria-label="Dark glass building facade photograph">
    <h4>Governance<br>considerations in<br>multi-jurisdictional<br>analysis</h4>
  </article>
  <article class="insight-card card-c" role="img" aria-label="Red geometric architecture against sky photograph">
    <h4 style="bottom:52px">Observations on<br>actuarial practice in<br>emerging markets</h4>
  </article>
</section>

<section class="cta" role="img" aria-label="Blue curved architectural facade background">
  <h2 class="display">Interested in exploring the platform?</h2>
  <div class="btn" style="left:488px;top:207px;width:225px;height:30px">Request Technical Walkthrough</div>
</section>

<footer class="site-footer">
  <div class="wordmark"><span>QP Fiduciary</span><span class="dot"></span></div>
  <nav class="footer-nav">
    <a style="left:351px">Company</a>
    <a style="left:451px">Platform</a>
    <a style="left:542px">Solutions</a>
    <a style="left:640px">Insights</a>
    <a style="left:727px">Contact</a>
  </nav>
  <span class="social" aria-label="Social profile"></span>
  <p class="copyright">© 2026 | www.qp-fiduciary.example</p>
</footer>

</body>
</html>
```